BrindleStaffing Business Card Design

We are a staffing company finding positions for dedicated nurses and physicians.

Target Market(s)

Business Professionals

Industry/Entity Type

Staffing

Contact Information for Business Card

Gordon Pratley
Chairman
417 39th Avenue South
SAINT PETERSBURG FL 33712
813-555-4172 Mobile
813-555-8036 Fax
gpratley@brindlestaffing.com
www.brindlestaffing.com

Font styles to use
Sans Serif

Colors
fbee3e
f04a50
f37122

Requirements
Must have
• Logo Attached, see colors below. We'd like to see Yellow, Orange and Red.

```html
<!DOCTYPE html>
<html lang="en">
<head>
<meta charset="utf-8">
<title>BrindleStaffing Business Card</title>
<link href="https://fonts.googleapis.com/css2?family=Lato:wght@400&family=Montserrat:wght@500;600&display=swap" rel="stylesheet">
<style>
  :root {
    --backdrop: #5b5b5b;
    --brand-yellow: #fbee3e;
    --brand-red: #f04a50;
    --brand-orange: #f37122;
    --paper: #f9f9f9;
    --white: #ffffff;
  }
  html, body {
    margin: 0;
    padding: 0;
    width: 1200px;
    height: 802px;
    overflow: hidden;
    background: var(--backdrop);
  }
  .stage {
    position: relative;
    width: 1200px;
    height: 802px;
  }
  .card {
    position: absolute;
    top: 274px;
    width: 442px;
    height: 264px;
    overflow: hidden;
    box-shadow: 0 2px 6px rgba(0,0,0,0.35);
  }
  .card--front { left: 136px; background: var(--brand-orange); }
  .card--back  { left: 624px; background: var(--paper); }

  .front__accent {
    position: absolute;
    top: 0; left: 0;
    width: 81px; height: 100%;
    background: var(--brand-red);
  }
  .front__cross-upright {
    position: absolute;
    top: 0; left: 81px;
    width: 108px; height: 100%;
    background: var(--white);
  }
  .front__cross-bar {
    position: absolute;
    top: 79px; left: 0;
    width: 270px; height: 108px;
    background: var(--white);
  }
  .front__details {
    position: absolute;
    right: 22px;
    top: 0;
    text-align: right;
    color: var(--white);
    font-family: "Lato", sans-serif;
  }
  .holder-name {
    position: absolute;
    right: 0;
    top: 34px;
    margin: 0;
    white-space: nowrap;
    font-family: "Montserrat", sans-serif;
    font-weight: 600;
    font-size: 19.5px;
  }
  .address, .contacts {
    position: absolute;
    right: 0;
    margin: 0;
    padding: 0;
    list-style: none;
    white-space: nowrap;
    font-size: 12.8px;
    line-height: 16px;
  }
  .address { top: 137px; }
  .contacts { top: 192px; }
  .contacts li { display: flex; justify-content: flex-end; align-items: center; gap: 3px; }
  .contacts svg { width: 10px; height: 10px; fill: var(--white); }

  .back__brand {
    position: absolute;
    left: 0; right: 0;
    top: 114px;
    display: flex;
    justify-content: center;
    align-items: center;
    gap: 10px;
  }
  .back__mark {
    width: 16px; height: 16px;
    background: var(--brand-yellow);
  }
  .back__name {
    margin: 0;
    font-family: "Montserrat", sans-serif;
    font-weight: 600;
    font-size: 33px;
    color: var(--brand-red);
    letter-spacing: -0.5px;
  }
  .back__web {
    position: absolute;
    left: 0; right: 0;
    top: 226px;
    text-align: center;
    font-family: "Lato", sans-serif;
    font-size: 13px;
    color: var(--brand-orange);
  }
</style>
</head>
<body>
<main class="stage">
  <section class="card card--front" aria-label="Business card front">
    <div class="front__accent"></div>
    <div class="front__cross-upright"></div>
    <div class="front__cross-bar"></div>
    <div class="front__details">
      <h1 class="holder-name">Gordon Pratley</h1>
      <p class="address">417 39th Avenue South<br>SAINT PETERSBURG<br>FL 33712</p>
      <ul class="contacts">
        <li>813-555-4172
          <svg viewBox="0 0 10 10" aria-hidden="true"><path d="M0 3.5C0 1.5 2 1 5 1s5 .5 5 2.5v1H7.5V3.3H2.5v1.2H0z"/><path d="M2 5h6l1 4H1z"/></svg>
        </li>
        <li>gpratley@brindlestaffing.com
          <svg viewBox="0 0 10 10" aria-hidden="true"><path d="M0 2h10v6H0z"/><path d="M0 2l5 3.5L10 2" fill="none" stroke="#f37122" stroke-width="1"/></svg>
        </li>
        <li>www.brindlestaffing.com
          <svg viewBox="0 0 10 10" aria-hidden="true"><circle cx="5" cy="5" r="5"/><path d="M3 3.2l2 .6 1.4 2-1.6 1.6L3.6 6z" fill="#f37122"/></svg>
        </li>
      </ul>
    </div>
  </section>

  <section class="card card--back" aria-label="Business card back">
    <div class="back__brand">
      <span class="back__mark"></span>
      <h2 class="back__name">BrindleStaffing</h2>
    </div>
    <div class="back__web">www.brindlestaffing.com</div>
  </section>
</main>
</body>
</html>
```